Business Cards for a law firm

Business cards for our law firm. Use our silhoette logo and OAK PARTNERS - check our website (www.oakpartners.example)

Contact Information for Business Card

our silhouette logo, OAK PARTNERS, 800-555-0147, Dorian Pemberton, dorian@oakpartners.example

Requirements
Must have
• our silhouette logo, OAK PARTNERS, 800-555-0147, Dorian Pemberton, dorian@oakpartners.example

```html
<!DOCTYPE html>
<html lang="en">
<head>
<meta charset="utf-8">
<title>Oak Partners – Business Cards</title>
<link rel="stylesheet" href="https://fonts.googleapis.com/css2?family=Noto+Sans:wght@400;700&display=swap">
<style>
  :root {
    --backdrop: #e5e5e5;
    --card: #ffffff;
    --navy: #0a1185;
    --ink: #333333;
    --name-ink: #111111;
    --band-grey: #bfc9c8;
    --band-dark: #272b27;
  }
  html, body {
    margin: 0;
    width: 1200px;
    height: 1200px;
    overflow: hidden;
    background: var(--backdrop);
  }
  .card {
    position: absolute;
    left: 205px;
    width: 790px;
    height: 451px;
    background: var(--card);
  }
  .card--front { top: 129px; }
  .card--back { top: 620px; }
  .card svg { display: block; width: 100%; height: 100%; }
  .contact-text {
    font-family: "Noto Sans", sans-serif;
    font-size: 30px;
    fill: var(--ink);
  }
  .holder-name {
    font-family: "Noto Sans", sans-serif;
    font-size: 50px;
    fill: var(--name-ink);
  }
  .firm-name {
    font-family: "Noto Sans", sans-serif;
    font-weight: 700;
    font-size: 74px;
    fill: var(--navy);
  }
  .accent { fill: var(--navy); }
  .band-grey { fill: var(--band-grey); }
  .band-dark { fill: var(--band-dark); }
  .icon-line { fill: none; stroke: var(--navy); stroke-width: 3; }
</style>
</head>
<body>

<section class="card card--front" aria-label="Card front">
  <svg viewBox="0 0 1272 727" xmlns="http://www.w3.org/2000/svg">
    <g class="contact-list" text-anchor="end">
      <text class="contact-text" x="627" y="288">800-555-0147</text>
      <text class="contact-text" x="627" y="341">dorian@oakpartners.example</text>
      <text class="contact-text" x="627" y="398">Www.yourweb.com</text>
      <text class="contact-text" x="627" y="463">Your Street,City,State,Pin Code,Country</text>
    </g>

    <g class="contact-icons">
      <path class="accent" d="M650 257c3-2 6-2 8 1l3 6c1 2 1 4-2 6l-2 2c2 4 5 7 9 9l2-2c2-2 4-3 6-1l6 3c2 2 3 5 1 7l-2 2c-3 3-10 2-18-3-8-6-13-13-14-20 0-4 1-7 3-10z"/>
      <rect class="icon-line" x="646" y="315" width="33" height="23" rx="3"/>
      <polyline class="icon-line" points="647,317 662.5,330 678,317"/>
      <g class="icon-line" style="stroke-width:2">
        <circle cx="661" cy="388" r="16"/>
        <ellipse cx="661" cy="388" rx="7" ry="16"/>
        <line x1="645" y1="388" x2="677" y2="388"/>
        <line x1="648" y1="380" x2="674" y2="380"/>
        <line x1="648" y1="396" x2="674" y2="396"/>
        <line x1="661" y1="372" x2="661" y2="404"/>
      </g>
      <path class="accent" d="M661 437c-8 0-14 6-14 14 0 9 14 24 14 24s14-15 14-24c0-8-6-14-14-14zm0 8a6 6 0 1 1 0 12a6 6 0 1 1 0-12z" fill-rule="evenodd"/>
    </g>

    <line x1="705" y1="243" x2="705" y2="483" stroke="var(--navy)" stroke-width="3"/>

    <g class="holder">
      <circle class="accent" cx="757" cy="334" r="15"/>
      <path class="accent" d="M728 373c0-14 10-22 20-22h18c10 0 20 8 20 22z"/>
      <text class="holder-name" x="803" y="368">Dorian Pemberton</text>
    </g>

    <g class="band">
      <rect class="band-grey" x="0" y="665" width="560" height="22"/>
      <rect class="accent" x="575" y="665" width="120" height="22"/>
      <rect class="band-dark" x="710" y="665" width="562" height="22"/>
    </g>
  </svg>
</section>

<section class="card card--back" aria-label="Card back">
  <svg viewBox="0 0 1272 727" xmlns="http://www.w3.org/2000/svg">
    <rect class="accent" x="230" y="300" width="80" height="80"/>
    <text class="firm-name" x="355" y="372" textLength="720" lengthAdjust="spacing">OAK PARTNERS</text>

    <g class="band">
      <rect class="accent" x="345" y="655" width="150" height="22"/>
      <rect class="band-dark" x="510" y="655" width="762" height="22"/>
    </g>
  </svg>
</section>

</body>
</html>
```